Business Card for a mobile physiotherapy company

I need a layout for a business card for a mobile physiotherapy company.
Slogan is "Mobile Physiotherapy - Your Road To Recovery"
Phone number is 867-555-0142
Email VardenTherapy@postnest.ca (subject to change with website)
Website www.VardenTherapy.ca
My name and credentials: Luke Varden Luke Varden, BSc(kin), MPT, CAFCI, IMS
Information maybe included: Direct Billing, Services including Physiotherapy, IMS, acupuncture
Maybe include facebook and instagram logos
One side with the logo clean and sharp
Other side with details, try not to look too busy, keep everything concise

```html
<!DOCTYPE html>
<html lang="en">
<head>
<meta charset="utf-8">
<title>Varden Therapy – Business Card</title>
<link href="https://fonts.googleapis.com/css2?family=Noto+Serif:wght@400;700&display=swap" rel="stylesheet">
<style>
  :root {
    --backdrop: #3a3b3e;
    --card: #1d1e21;
    --blue: #24608f;
    --green: #2f7d5c;
    --text: #e9e9ea;
    --muted: #c9c9cc;
  }
  * { box-sizing: border-box; margin: 0; padding: 0; }
  html, body { width: 799px; height: 1200px; overflow: hidden; }
  body {
    background: var(--backdrop);
    font-family: "Noto Serif", Georgia, serif;
    color: var(--text);
    position: relative;
  }
  .card {
    position: absolute;
    left: 80px;
    width: 640px;
    height: 366px;
    background: var(--card);
    border-radius: 22px;
    overflow: hidden;
    box-shadow: 0 10px 30px rgba(0,0,0,.45);
  }
  .card--front { top: 150px; }
  .card--back { top: 684px; }
  .edge-band {
    position: absolute; left: 0; right: 0; bottom: 0; height: 7px;
    background: linear-gradient(90deg, var(--green), var(--blue));
  }
  .brand {
    position: absolute;
    display: flex; align-items: center; gap: 12px;
    color: var(--green);
    font-weight: 700;
    line-height: 1.05;
  }
  .brand__mark {
    width: 16px; height: 16px; background: var(--green);
  }
  .card--front .brand { left: 200px; top: 112px; font-size: 46px; letter-spacing: 2px; }
  .card--front .brand .brand__mark { width: 20px; height: 20px; }
  .services {
    position: absolute; left: 34px; right: 34px; bottom: 34px;
    font-size: 15px; color: var(--text); text-align: center; white-space: nowrap;
  }
  .accent-arc {
    position: absolute; left: -22px; top: 28px;
    width: 44px; height: 44px; border-radius: 50%;
    background: var(--green);
  }
  .person { position: absolute; left: 44px; top: 32px; }
  .person__name {
    font-size: 24px; font-weight: 700; color: var(--blue);
    text-transform: uppercase; letter-spacing: 1px;
  }
  .person__credentials { font-size: 12px; color: var(--muted); margin-top: 2px; }
  .contact { position: absolute; left: 34px; top: 172px; font-size: 15px; }
  .follow { display: flex; align-items: center; gap: 8px; margin-bottom: 8px; }
  .social-dot { width: 22px; height: 22px; border-radius: 50%; background: var(--blue); }
  .social-dot--alt { background: #b23f7c; }
  .contact__row { display: flex; align-items: center; gap: 12px; line-height: 1.55; }
  .contact__row svg { width: 13px; height: 13px; flex: none; }
  .card--back .brand { right: 40px; top: 140px; font-size: 34px; letter-spacing: 1.5px; }
  .slogan {
    position: absolute; right: 40px; bottom: 36px;
    font-size: 17px; text-align: right; line-height: 1.35;
  }
</style>
</head>
<body>
  <section class="card card--front">
    <div class="brand">
      <span class="brand__mark"></span>
      <span>VARDEN<br>THERAPY</span>
    </div>
    <p class="services">Direct Billing | Services Including Physiotherapy | IMS | Acupuncture</p>
    <div class="edge-band"></div>
  </section>

  <section class="card card--back">
    <div class="accent-arc"></div>
    <div class="person">
      <h1 class="person__name">Luke Varden</h1>
      <p class="person__credentials">BSc(kin), MPT, CAFCI, IMS</p>
    </div>

    <div class="contact">
      <div class="follow">
        <span>Follow us on:</span>
        <span class="social-dot"></span>
        <span class="social-dot social-dot--alt"></span>
      </div>
      <div class="contact__row">
        <svg viewBox="0 0 16 16" aria-hidden="true"><path fill="#2f7d5c" d="M3 1h3l1.5 4-2 1.2a9 9 0 0 0 4.3 4.3L11 8.5l4 1.5v3a2 2 0 0 1-2 2A12 12 0 0 1 1 3a2 2 0 0 1 2-2z"/></svg>
        <span>867-555-0142</span>
      </div>
      <div class="contact__row">
        <svg viewBox="0 0 16 16" aria-hidden="true"><rect x="1" y="3" width="14" height="10" fill="#2f7d5c"/><path d="M1 3l7 6 7-6" stroke="#1d1e21" stroke-width="1.4" fill="none"/></svg>
        <span>VardenTherapy@postnest.ca</span>
      </div>
      <div class="contact__row">
        <svg viewBox="0 0 16 16" aria-hidden="true"><circle cx="8" cy="8" r="6.5" fill="none" stroke="#2f7d5c" stroke-width="1.5"/><path d="M1.5 8h13M8 1.5c-3 3.5-3 9.5 0 13M8 1.5c3 3.5 3 9.5 0 13" stroke="#2f7d5c" stroke-width="1.2" fill="none"/></svg>
        <span>www.VardenTherapy.ca</span>
      </div>
    </div>

    <div class="brand">
      <span class="brand__mark"></span>
      <span>VARDEN<br>THERAPY</span>
    </div>

    <p class="slogan">Mobile Physiotherapy<br>Your Road To Recovery</p>
    <div class="edge-band"></div>
  </section>
</body>
</html>
```